Corporate Business Card

Very professional, Modern, Not to busy, include phone address email, website
(253) 617-4930, 18761 52nd Avenue S, Alder Bay, OR 98047, martin@plumlinegroup.com, varkoworks.com

Target Market(s)

Manufacturing

Industry/Entity Type

Aero, machining, manufacturing, Off road racing

Contact Information for Business Card

Phone, address email, website

```html
<!DOCTYPE html>
<html lang="en">
<head>
<meta charset="utf-8">
<title>Varko Works – Business Card</title>
<link href="https://fonts.googleapis.com/css2?family=Exo+2:wght@400;500;700&display=swap" rel="stylesheet">
<style>
  :root {
    --backdrop: #2a2321;
    --card: #1b1b1c;
    --blue: #1b3a7a;
    --red: #d8232e;
    --ink: #f2f2f2;
  }
  * { margin: 0; padding: 0; box-sizing: border-box; }
  html, body { width: 1200px; height: 842px; overflow: hidden; }
  body {
    background: var(--backdrop);
    font-family: "Exo 2", sans-serif;
    position: relative;
  }
  .card {
    position: absolute;
    top: 267px;
    width: 540px;
    height: 308px;
    background: var(--card);
    overflow: hidden;
    box-shadow: 0 12px 30px rgba(0,0,0,.45);
  }
  .card--back { left: 40px; }
  .card--front { left: 620px; }

  /* back side */
  .band { position: absolute; left: 0; right: 0; background: var(--blue); }
  .band--top { top: 0; height: 14px; }
  .band--bottom { bottom: 0; height: 16px; border-bottom: 2px solid var(--red); }
  .contact {
    position: absolute;
    inset: 38px 0 30px;
    display: flex;
    flex-direction: column;
    align-items: center;
    text-align: center;
    color: var(--ink);
  }
  .contact__name {
    color: var(--blue);
    font-weight: 700;
    font-size: 21px;
    letter-spacing: .5px;
    text-transform: uppercase;
    line-height: 1;
  }
  .contact__title {
    color: var(--red);
    font-size: 15px;
    font-weight: 500;
    letter-spacing: .5px;
    margin-top: 2px;
  }
  .divider {
    width: 120px;
    height: 1px;
    background: var(--blue);
    margin: 9px 0;
  }
  .contact__line { font-size: 15px; line-height: 1.3; letter-spacing: .3px; }
  .contact__address { font-size: 17px; line-height: 1.25; letter-spacing: .3px; }

  /* front side */
  .edge-mark { position: absolute; top: 96px; height: 116px; }
  .edge-mark__block { position: absolute; top: 0; width: 28px; height: 100%; background: var(--blue); }
  .edge-mark__stripe { position: absolute; top: 0; width: 4px; height: 100%; background: var(--red); }
  .edge-mark--left { left: 0; }
  .edge-mark--left .edge-mark__block { left: 0; }
  .edge-mark--left .edge-mark__stripe { left: 36px; }
  .edge-mark--right { right: 0; }
  .edge-mark--right .edge-mark__block { right: 0; }
  .edge-mark--right .edge-mark__stripe { right: 36px; }
  .brand {
    position: absolute;
    left: 0; right: 0; top: 118px;
    text-align: center;
  }
  .brand__name {
    color: var(--blue);
    font-weight: 700;
    font-size: 50px;
    letter-spacing: 3px;
    text-transform: uppercase;
    line-height: 1;
  }
  .brand__rule {
    width: 190px;
    height: 2px;
    background: var(--blue);
    margin: 12px auto 0;
  }
</style>
</head>
<body>
  <section class="card card--back">
    <div class="band band--top"></div>
    <div class="contact">
      <p class="contact__name">Daniel Reyes</p>
      <p class="contact__title">Managing Director</p>
      <div class="divider"></div>
      <p class="contact__line">(541) 617-4930</p>
      <p class="contact__line">martin@plumlinegroup.com</p>
      <p class="contact__line">www.varkoworks.com</p>
      <div class="divider"></div>
      <p class="contact__address">18761 52nd Avenue S</p>
      <p class="contact__address">Alder Bay, OR 98047</p>
    </div>
    <div class="band band--bottom"></div>
  </section>

  <section class="card card--front">
    <div class="edge-mark edge-mark--left">
      <div class="edge-mark__block"></div>
      <div class="edge-mark__stripe"></div>
    </div>
    <div class="brand">
      <p class="brand__name">Varko Works</p>
      <div class="brand__rule"></div>
    </div>
    <div class="edge-mark edge-mark--right">
      <div class="edge-mark__block"></div>
      <div class="edge-mark__stripe"></div>
    </div>
  </section>
</body>
</html>
```